Brochure for a website accessibility report

This brochure is related to a report that www.qelvantrix.org sell. The report shows the results of an automated audit of a websites accessibility. It shows details of issues found with screen shots, examples of code and provides remediation advice.

The brochure will be a pdf 8.5 inches by 11 inches. It can be anywhere from 6 to 10 pages.

The FlintVue™ name itself should be “Bree Serif” font. The fonts, styles, colors and sizes are up to you.

The images used and logo of the Office of Digital Reachworks and K7P logo are upload

We highlighted in blue page extracts from the report we sell. Do not use the blue highlight, it is merely there to show you where the specific examples of the report we sell are vs the other content in the report. The areas in blue which show the content from the actual report should be shown as an extract of the actual page of the report. You have flexibility to change the layout and the way the content look.

The red square callouts over the blue content are callouts that describe the specific page extracts. We used it as a red callout only so that you would be able to see it. You should change the specific location, look and feel of the callout to be appropriate

Target Market(s)

Marketing and Technical people

Industry/Entity Type

Information Technology

Font styles to use
Sans Serif

Colors

Designer to choose colors to be used in the design.

Requirements
Should not have
• wheelchairs, images of blind people

```html
<!DOCTYPE html>
<html lang="en">
<head>
<meta charset="UTF-8">
<title>FlintVue™ Accessibility Report – WCAG Principles</title>
<link href="https://fonts.googleapis.com/css2?family=Bree+Serif&family=Roboto:wght@300;400;500;700&display=swap" rel="stylesheet">
<style>
  :root {
    --page-bg: #ffffff;
    --body-text: #5a5a5a;
    --lead-text: #1f4a3c;
    --card-bg: #0d3a5c;
    --card-text: #ffffff;
    --accent-yellow: #f6c431;
    --accent-cyan: #35d3e3;
    --panel-bg: #e7e7e7;
    --brand-blue: #1260a8;
  }
  * { box-sizing: border-box; margin: 0; padding: 0; }
  html, body {
    width: 928px; height: 1200px; overflow: hidden;
    background: var(--page-bg);
  }
  body {
    position: relative;
    font-family: "Roboto", Arial, sans-serif;
    color: var(--body-text);
  }
  .intro {
    position: absolute; left: 52px; top: 79px; width: 824px;
    font-size: 16px; line-height: 20px; font-weight: 300;
    text-align: justify;
  }
  .partner-mark {
    position: absolute; left: 52px; top: 210px;
    display: flex; align-items: center; gap: 10px;
  }
  .partner-mark .square {
    width: 34px; height: 34px; background: var(--brand-blue);
  }
  .partner-mark .name {
    font-size: 30px; font-weight: 700; color: var(--brand-blue); letter-spacing: 1px;
  }
  .lead {
    position: absolute; left: 52px; top: 278px;
    font-size: 16px; color: var(--lead-text);
  }
  .principle {
    position: absolute;
    background: var(--card-bg);
    border-radius: 27px;
    padding: 30px 31px 0;
    color: var(--card-text);
    box-shadow: 0 6px 14px rgba(0,0,0,0.18);
  }
  .principle .label {
    font-size: 13px; font-weight: 500; letter-spacing: .2px;
  }
  .principle h2 {
    font-family: "Bree Serif", Georgia, serif;
    font-weight: 400; font-size: 31px; line-height: 38px;
    color: var(--accent-yellow); margin: 2px 0 10px;
  }
  .principle p {
    font-size: 14.5px; line-height: 18px; font-weight: 400;
  }
  .principle .key {
    margin-top: 10px; color: var(--accent-cyan); font-weight: 500; font-size: 14.5px;
  }
  .p1 { left: 52px; top: 327px; width: 396px; height: 219px; }
  .p2 { left: 480px; top: 327px; width: 396px; height: 207px; }
  .p3 { left: 52px; top: 580px; width: 396px; height: 209px; }
  .p4 { left: 481px; top: 567px; width: 395px; height: 222px; }
  .report-panel {
    position: absolute; left: 52px; top: 839px; width: 876px; height: 361px;
    background: var(--panel-bg);
    border-top-left-radius: 64px;
    padding: 49px 52px 0 51px;
  }
  .report-panel p {
    font-size: 16px; line-height: 20px; font-weight: 300;
    text-align: justify; margin-bottom: 20px;
  }
  .brand { font-family: "Bree Serif", Georgia, serif; font-weight: 400; }
  .report-panel ul { list-style: none; margin-top: 8px; }
  .report-panel li {
    position: relative; padding-left: 32px;
    font-size: 13.6px; line-height: 18px; font-weight: 300;
    text-align: justify; margin-bottom: 20px;
  }
  .report-panel li::before {
    content: ""; position: absolute; left: 4px; top: 7px;
    width: 6px; height: 6px; background: var(--accent-cyan);
  }
</style>
</head>
<body>
  <p class="intro">The Americans with Disabilities Act (ADA) is a comprehensive federal civil rights law prohibiting discrimination on the basis of disability, enforced by the Department of Justice (DOJ). The ADA prohibits discriminatory lack of access for individuals with disabilities to goods and services of public services and accommodations. Websites are considered places of public accommodations. The DOJ currently uses WCAG 2.1 Level A/AA as an accepted standard by which to measure a website’s accessibility.</p>

  <div class="partner-mark">
    <span class="square"></span>
    <span class="name">K7P</span>
  </div>

  <p class="lead">WCAG 2.1 Level A/AA consists of 13 guidelines with 50 checkpoints that are organized under four principles:</p>

  <section class="principle p1">
    <div class="label">PRINCIPLE 1</div>
    <h2>Perceivable</h2>
    <p>Information and user interface components must be presented to users in ways they can perceive. This means that users must be able to compre-hend the information being depicted:</p>
    <p class="key">It can’t be invisible to all their senses.</p>
  </section>

  <section class="principle p2">
    <div class="label">PRINCIPLE 2</div>
    <h2>Operable</h2>
    <p>User interface components and navigation must be operable:</p>
    <p class="key">The interface cannot require interaction that a user cannot perform.</p>
  </section>

  <section class="principle p3">
    <div class="label">PRINCIPLE 3</div>
    <h2>Understandable</h2>
    <p>Information and the operation of a user interface must be understandable:</p>
    <p class="key">Users must be able to understand the information as well as the operation of the user interface.</p>
  </section>

  <section class="principle p4">
    <div class="label">PRINCIPLE 4</div>
    <h2>Robust</h2>
    <p>Content must be robust enough that it can be interpreted reliably by a wide variety of user agents, including assistive technologies:</p>
    <p class="key">As technologies and user agents evolve, the content should remain accessible.</p>
  </section>

  <section class="report-panel">
    <p>Start your journey to a fully compliant website with <span class="brand">FlintVue™</span>. This detailed compliance and remediation report is generated based on scanning your website against hundreds of carefully-crafted rules, logging failures, and then generating feedback and recommendations on how to fix the problems based on our years of experience and proven best practices.</p>
    <p>The <span class="brand">FlintVue™</span> report is designed to be shared with your executive team and stakeholders. It is divided into two sections to build knowledge and self-sufficiency.</p>
    <ul>
      <li>The first section provides a detailed analysis of your website per the WCAG 2.1 A/AA principles and includes an at-a-glance Summary Chart for your executive team.</li>
      <li>The second section is designed specifically for your website development team, providing them with detailed examples of problematic issues, suggested ways to fix them, and links for more detailed training.</li>
    </ul>
  </section>
</body>
</html>
```